Business Card Design for Vintage Jazz

I am a vintage jazz band leader in New York City. My groups play the music of the 1920s, 1930s and 1940s. My website is morvalquist.com for more info on what I do.

I am looking for a two sided business card design that has the look and feel of a really nice business card from the 1930s. I need to convey with the design that my work has that vintage kind of class and style, but also conveys that we are fun and entertaining.

Most importantly it should make a bold staement. If Hal Denbrook had a card, what would it have looked like? I want a card that I feel confident will make an impact and will let people know that my work is te the top that NYC has to offer in vintage jazz..

Note that I have only decided to avoid the "committed payment" option as I have not used this service before. Assuming that I get quality work I will select a design from those presented.

Target Market(s)

people who want to hire my band for events, media, and new fans of the band

Industry/Entity Type

Performing Art

Contact Information for Business Card

Definitely a matte finish, possibly a sort of old style of paper with that brown tint? definitely a thick card.

Requirements
Must have
• FRONT
• My name: Tobin Vashley
• What I do: Bandleader, Guitarist, Vocalist, Songwriter
• Contact Details: morvalquist.com tobin@morvalquist.com 646-555-0148
• BACK
• My Social Media Links:
• facebook.morvalquist.com
• twitter, instagram, linkedin: morvalquist
• I'm also including a photo image I would like to use. The photo's background is not needed, and to be honest isn't really desireable. Just looking to use the image of me.
Nice to have
• I'm attaching which could be used as is, omitted from the card, or altered maybe with text going around the outside of the circle or in some other way. It may need some clean up to the edges of the lettering as we only use it for the website thumbnail.
• If there's space I'd like to include the text "join our mailing list for a free song download: freesong.morvalquist.com" If not perhaps just "Download a Free Song at: freesong.morvalquist.com - something to this end.
Should not have
• anything cartoony. Don't think retro 90s's vision of the swing era, think actual swing era!
• anything modern. Got to look old school
• Try to avoid dark backgrounds. Since we often play in bars and clubs where it is dar, a d
• avoid script fonts.

```html
<!DOCTYPE html>
<html lang="en">
<head>
<meta charset="utf-8">
<title>Tobin Vashley – Business Card</title>
<link href="https://fonts.googleapis.com/css2?family=Open+Sans:wght@400;600;700&display=swap" rel="stylesheet">
<style>
  :root {
    --stage: #d9d2c5;
    --card-paper: #efe2c6;
    --card-paper-edge: #e2d0ad;
    --ink: #2b2118;
    --ink-soft: #4a3a2b;
    --band-tan: #a88a5e;
    --band-text: #fbf4e4;
    --disc-ink: #2b2118;
    --disc-text: #efe2c6;
    --photo-tone: #8f9c8a;
    --photo-tone-dark: #6d7a69;
  }
  * { margin: 0; padding: 0; box-sizing: border-box; }
  html, body {
    width: 1200px; height: 900px; overflow: hidden;
    background: var(--stage);
    font-family: "Open Sans", Arial, sans-serif;
  }
  .canvas { position: relative; width: 1200px; height: 900px; }
  .card {
    position: absolute; left: 255px; width: 690px; height: 395px;
    background: radial-gradient(ellipse at 50% 40%, var(--card-paper) 60%, var(--card-paper-edge));
    border-radius: 26px; overflow: hidden;
    color: var(--ink);
    box-shadow: 0 2px 6px rgba(60, 40, 20, 0.25);
  }
  .card--back { top: 40px; }
  .card--front { top: 465px; }

  /* Shared mark */
  .brand-disc {
    position: absolute; border-radius: 50%;
    background: var(--disc-ink); color: var(--disc-text);
    display: flex; align-items: center; justify-content: center;
    font-weight: 700; letter-spacing: 1px; text-transform: uppercase;
  }

  /* Back side */
  .card--back .brand-disc {
    left: 230px; top: 30px; width: 230px; height: 230px; font-size: 26px;
  }
  .free-song { position: absolute; left: 40px; bottom: 40px; width: 320px; }
  .free-song__label { font-size: 19px; font-weight: 700; letter-spacing: 1.5px; text-transform: uppercase; white-space: nowrap; }
  .free-song__url { font-size: 16px; margin-top: 8px; color: var(--ink-soft); }
  .divider {
    position: absolute; left: 372px; bottom: 40px; width: 2px; height: 58px;
    background: var(--ink);
  }
  .social { position: absolute; left: 390px; bottom: 40px; font-size: 16px; line-height: 29px; }
  .social__row { display: flex; align-items: center; gap: 8px; }
  .social__dot { width: 12px; height: 12px; border-radius: 50%; background: var(--ink); display: inline-block; }

  /* Front side */
  .band {
    position: absolute; left: 0; right: 0; top: 130px; height: 145px;
    background: var(--band-tan);
  }
  .card--front .brand-disc {
    left: 50px; top: 108px; width: 190px; height: 190px; font-size: 21px;
    border: 5px solid var(--card-paper); z-index: 2;
  }
  .identity {
    position: absolute; left: 255px; top: 134px; z-index: 2;
    text-align: right; width: 230px; color: var(--band-text);
  }
  .identity__name { font-size: 26px; font-weight: 700; text-transform: uppercase; letter-spacing: 0.5px; line-height: 30px; white-space: nowrap; }
  .identity__role { font-size: 14px; text-transform: uppercase; line-height: 17px; letter-spacing: 0.5px; }
  .contact { margin-top: 8px; font-size: 14px; line-height: 18px; }
  .contact b { font-weight: 700; }
  .portrait {
    position: absolute; left: 500px; top: 60px; width: 160px; height: 160px;
    border-radius: 50%; border: 5px solid var(--ink);
    background: radial-gradient(circle at 50% 45%, var(--photo-tone), var(--photo-tone-dark));
    z-index: 2;
  }
</style>
</head>
<body>
<main class="canvas">

  <section class="card card--back" aria-label="Card back">
    <div class="brand-disc">Morvalquist</div>
    <div class="free-song">
      <p class="free-song__label">Download a free song at</p>
      <p class="free-song__url">www.freesong.morvalquist.com</p>
    </div>
    <div class="divider"></div>
    <div class="social">
      <p class="social__row"><span class="social__dot"></span>facebook.morvalquist.com</p>
      <p class="social__row"><span class="social__dot"></span>morvalquist</p>
    </div>
  </section>

  <section class="card card--front" aria-label="Card front">
    <div class="band"></div>
    <div class="brand-disc">Morvalquist</div>
    <div class="identity">
      <h1 class="identity__name">Tobin Vashley</h1>
      <p class="identity__role">Bandleader, Guitarist</p>
      <p class="identity__role">Vocalist, Songwriter</p>
      <div class="contact">
        <p><b>P:</b> 646-555-0148</p>
        <p><b>E:</b> tobin@morvalquist.com</p>
        <p><b>W:</b> www.morvalquist.com</p>
      </div>
    </div>
    <div class="portrait" role="img" aria-label="Photo of the bandleader in a suit tipping a straw hat"></div>
  </section>

</main>
</body>
</html>
```